ULMIRA card Technical Architecture

Hello everyone ULMIRA: It is a consulting firm in Architecture and Construction. I require a card duplexing, sober, elegant, classic but not boring. Update 1: Use the following data for the card. Name: Gonzalo Pereda Mauricio Villalta Position: COO Twitter: @ulmiraAT Homepage: ulmira-example.com home address not include the participation of all thank you.

Target Market(s)

Construction companies, Architects and Consulting Engineers

Industry/Entity Type

Consulting

Contact Information for Business Card

Los campos que debe tener:
Nombre, Cargo, email, homepage y twitter

Font styles to use
Serif
Sans Serif
Other font styles liked:
• Me gustan playfair display, open sans y roboto, pero estoy sujeto a sus propuestas

Requirements
Must have
• Colors: Present combined proposals in white, red, gray and black Update 1: The two names must be clearly differentiated from the two surnames
Nice to have
• They are free to present their best proposals. I will bring them immediate feedback to the extent you can go see their designs. Complete data for card and logo files will give the winner the

```html
<!DOCTYPE html>
<html lang="es">
<head>
<meta charset="utf-8">
<title>ULMIRA – Arquitectura Técnica business card</title>
<link rel="stylesheet" href="https://fonts.googleapis.com/css2?family=Montserrat:wght@400;500&family=Open+Sans:wght@400;700&display=swap">
<style>
  :root {
    --page-bg: #e9e7e4;
    --brand-red: #c00010;
    --brand-red-deep: #6a0008;
    --brand-red-glow: #b8000f;
    --ink-black: #111111;
    --paper-white: #ffffff;
    --line-red: #a3121c;
  }
  * { box-sizing: border-box; margin: 0; padding: 0; }
  html, body {
    width: 1200px; height: 900px; overflow: hidden;
    background: var(--page-bg);
  }
  .sheet {
    width: 1200px; height: 900px;
    display: flex; align-items: center; justify-content: center; gap: 40px;
  }
  .card {
    width: 540px; height: 309px;
    position: relative; overflow: hidden;
    box-shadow: 0 10px 24px rgba(0,0,0,.18);
  }

  /* Wordmark shared */
  .wordmark { text-align: center; }
  .wordmark__name {
    font-family: "Montserrat", sans-serif;
    font-weight: 400;
    letter-spacing: .32em;
    padding-left: .32em;
    line-height: 1;
  }
  .wordmark__rule { height: 1px; margin: 10px auto 6px; }
  .wordmark__tagline {
    font-family: "Montserrat", sans-serif;
    font-weight: 500;
    letter-spacing: .36em;
    padding-left: .36em;
    line-height: 1;
  }

  /* Front */
  .card--front {
    background: radial-gradient(ellipse 70% 75% at 62% 30%, var(--brand-red-glow) 0%, #97000c 55%, var(--brand-red-deep) 100%);
    display: flex; align-items: center; justify-content: center;
  }
  .card--front .wordmark__name { color: var(--paper-white); font-size: 52px; }
  .card--front .wordmark__rule { width: 360px; background: rgba(255,255,255,.75); }
  .card--front .wordmark__tagline { color: var(--paper-white); font-size: 17px; }

  /* Back */
  .card--back { background: var(--paper-white); }
  .back__brand {
    height: 168px;
    display: flex; align-items: center; justify-content: center;
    padding-top: 14px;
  }
  .card--back .wordmark__name { color: var(--ink-black); font-size: 38px; }
  .card--back .wordmark__rule { width: 300px; background: var(--line-red); margin: 7px auto 5px; }
  .card--back .wordmark__tagline { color: var(--line-red); font-size: 13px; }

  .back__contact {
    height: 96px;
    background: var(--brand-red);
    position: relative;
    border-top: 4px solid var(--paper-white);
    color: var(--paper-white);
    font-family: "Open Sans", sans-serif;
  }
  .contact__row {
    position: absolute; top: 12px; left: 0; right: 0;
    display: flex; justify-content: center; align-items: center;
  }
  .person { text-align: right; padding-right: 12px; border-right: 1px solid rgba(255,255,255,.8); }
  .person__name { font-weight: 700; font-size: 15px; letter-spacing: .01em; }
  .person__role { font-size: 12.5px; margin-top: 1px; }
  .channels { padding-left: 10px; font-size: 12px; line-height: 1.5; }
  .channel { display: flex; align-items: center; gap: 6px; }
  .channel svg { width: 10px; height: 10px; fill: var(--paper-white); }
  .social {
    position: absolute; bottom: 10px; left: 50%; transform: translateX(10px);
    display: flex; gap: 8px;
  }
  .social__slot { width: 17px; height: 17px; background: var(--paper-white); border-radius: 2px; }

  .back__band {
    position: absolute; left: 0; right: 0; bottom: 0;
    height: 45px;
    background: var(--ink-black);
    border-top: 3px solid var(--paper-white);
  }
</style>
</head>
<body>
<main class="sheet">
  <section class="card card--front" aria-label="Card front">
    <div class="wordmark">
      <p class="wordmark__name">ULMIRA</p>
      <div class="wordmark__rule"></div>
      <p class="wordmark__tagline">ARQUITECTURA TÉCNICA</p>
    </div>
  </section>

  <section class="card card--back" aria-label="Card back">
    <div class="back__brand">
      <div class="wordmark">
        <p class="wordmark__name">ULMIRA</p>
        <div class="wordmark__rule"></div>
        <p class="wordmark__tagline">ARQUITECTURA TÉCNICA</p>
      </div>
    </div>
    <div class="back__contact">
      <div class="contact__row">
        <div class="person">
          <p class="person__name">MARTIN ROLES</p>
          <p class="person__role">Managing Director</p>
        </div>
        <div class="channels">
          <p class="channel">
            <svg viewBox="0 0 10 10" aria-hidden="true"><path d="M2.5 0h5a1 1 0 0 1 1 1v8a1 1 0 0 1-1 1h-5a1 1 0 0 1-1-1V1a1 1 0 0 1 1-1zm.5 1.5v6h4v-6zM5 8.2a.5.5 0 1 0 0 1 .5.5 0 0 0 0-1z"/></svg>
            (055)987654321
          </p>
          <p class="channel">
            <svg viewBox="0 0 10 10" aria-hidden="true"><path d="M0 2h10v6H0zm1 .8L5 5.6l4-2.8z" fill-rule="evenodd"/></svg>
            hello@ulmira-example.com
          </p>
        </div>
      </div>
      <div class="social">
        <span class="social__slot"></span>
        <span class="social__slot"></span>
      </div>
    </div>
    <div class="back__band"></div>
  </section>
</main>
</body>
</html>
```